QVR business card

Need a business card for a company that provides instructional design and elearning development services. The website is here: http://quorvane.studio/

I'm attaching a current logo, as well as the old business card design. While I like to keep it clean, the old design is too simplistic for my liking. The only idea I want to reuse from the old design is placing industry jargon on the back of the card, just need a better way to present it. But if you have other ideas for the back--feel free to experiment.

Please use the colors complementary to the color we have on the website. Thank you!

```html
<!DOCTYPE html>
<html lang="en">
<head>
<meta charset="utf-8">
<title>QVR Business Card</title>
<link href="https://fonts.googleapis.com/css2?family=Open+Sans:wght@400;600;700;800&family=PT+Sans+Narrow:wght@400;700&display=swap" rel="stylesheet">
<style>
  :root {
    --teal: #1fb1ae;
    --teal-dark: #179a97;
    --sand: #d9cd98;
    --ink: #333333;
    --paper: #ffffff;
    --backdrop: #e4e4e4;
    --rule: #b9b9b9;
  }
  html, body {
    margin: 0;
    padding: 0;
    width: 1200px;
    height: 873px;
    overflow: hidden;
    background: var(--backdrop);
  }
  .canvas {
    position: relative;
    width: 1200px;
    height: 873px;
    display: flex;
    align-items: center;
    justify-content: center;
    gap: 40px;
  }
  .card {
    position: relative;
    width: 540px;
    height: 310px;
    box-shadow: 0 6px 18px rgba(0,0,0,0.18);
    overflow: hidden;
    flex: none;
  }

  /* Front */
  .card--front { background: var(--paper); font-family: "Open Sans", sans-serif; }
  .card__decor { position: absolute; inset: 0; }
  .brand {
    position: absolute;
    left: 30px;
    top: 128px;
    display: flex;
    align-items: center;
    gap: 10px;
  }
  .brand__mark {
    width: 22px;
    height: 22px;
    background: var(--teal);
  }
  .brand__name {
    font-family: "Open Sans", sans-serif;
    font-weight: 700;
    font-size: 38px;
    color: var(--teal);
    letter-spacing: 1px;
    line-height: 1;
  }
  .divider {
    position: absolute;
    left: 268px;
    top: 112px;
    width: 1px;
    height: 80px;
    background: var(--rule);
  }
  .contact {
    position: absolute;
    left: 284px;
    top: 110px;
    color: var(--ink);
  }
  .contact__name {
    margin: 0;
    font-weight: 700;
    font-size: 13px;
    color: var(--teal);
    letter-spacing: 0.3px;
  }
  .contact__role {
    margin: 2px 0 18px;
    font-size: 12px;
  }
  .contact__line {
    display: flex;
    align-items: center;
    gap: 7px;
    font-size: 12px;
    margin: 0 0 4px;
  }
  .contact__icon { width: 11px; height: 11px; fill: var(--teal); }
  .website {
    position: absolute;
    right: 0;
    bottom: 0;
    width: 250px;
    height: 30px;
    display: flex;
    align-items: center;
    padding-left: 26px;
    box-sizing: border-box;
    font-size: 12px;
    color: var(--paper);
  }

  /* Back */
  .card--back {
    background: var(--teal);
    color: var(--paper);
    display: flex;
    align-items: center;
  }
  .back__headline {
    flex: none;
    margin: 0 0 0 24px;
    font-family: "Open Sans", sans-serif;
    font-weight: 700;
    font-size: 46px;
    line-height: 1.02;
    letter-spacing: 0.5px;
    white-space: nowrap;
  }
  .back__headline span { display: block; }
  .back__rule {
    flex: none;
    width: 2px;
    height: 260px;
    background: rgba(255,255,255,0.85);
    margin: 0 14px 0 14px;
  }
  .jargon {
    flex: none;
    list-style: none;
    margin: 0;
    padding: 0;
    font-family: "PT Sans Narrow", sans-serif;
    font-size: 28px;
    line-height: 1.28;
    text-transform: uppercase;
    white-space: nowrap;
  }
</style>
</head>
<body>
<main class="canvas">

  <section class="card card--front" aria-label="Business card front">
    <svg class="card__decor" width="540" height="310" viewBox="0 0 540 310" aria-hidden="true">
      <defs>
        <linearGradient id="edgeFade" x1="0" y1="0" x2="0" y2="1">
          <stop offset="0" stop-color="#1fb1ae"/>
          <stop offset="1" stop-color="#d9cd98"/>
        </linearGradient>
        <linearGradient id="bandFade" x1="0" y1="0" x2="1" y2="0">
          <stop offset="0" stop-color="#d9cd98"/>
          <stop offset="0.25" stop-color="#1fb1ae"/>
          <stop offset="1" stop-color="#1fb1ae"/>
        </linearGradient>
      </defs>
      <polygon points="0,150 14,164 14,310 0,310" fill="url(#edgeFade)"/>
      <polygon points="14,300 260,300 290,280 540,280 540,310 14,310" fill="url(#bandFade)"/>
    </svg>

    <div class="brand">
      <span class="brand__mark"></span>
      <span class="brand__name">QVR</span>
    </div>

    <div class="divider"></div>

    <div class="contact">
      <p class="contact__name">ADRIAN VELMONT</p>
      <p class="contact__role">Managing Director</p>
      <p class="contact__line">
        <svg class="contact__icon" viewBox="0 0 12 12" aria-hidden="true"><path d="M1 4c0-2 2-3 5-3s5 1 5 3l-2 1-1-1.5H4L3 5zM3 6h6l1 5H2z"/></svg>
        555-014-2287
      </p>
      <p class="contact__line">
        <svg class="contact__icon" viewBox="0 0 12 12" aria-hidden="true"><path d="M1 5l5-4 5 4v6H1zM2.5 5.5L6 8l3.5-2.5"/></svg>
        avelmont@quorvane.studio
      </p>
    </div>

    <div class="website">www.quorvane.studio</div>
  </section>

  <section class="card card--back" aria-label="Business card back">
    <h2 class="back__headline"><span>HOW</span><span>CAN</span><span>WE</span><span>HELP?</span></h2>
    <div class="back__rule"></div>
    <ul class="jargon">
      <li>Mobile Learning SCORM</li>
      <li>Instructional Design LMS</li>
      <li>MOOCs eLearning HTML5</li>
      <li>Adult Learning Theory</li>
      <li>Gamification Classroom</li>
      <li>xAPI Blended Learning</li>
    </ul>
  </section>

</main>
</body>
</html>
```